Walk Beside The River

Business Card design

Target Market(s)

People who require support in the commnity

Industry/Entity Type

Mental Health Support

Contact Information for Business Card

Mental Health Support Rosalind Tavener walkbesidetheriver@mailcove.com.au 0481 637 092 PO Box 926 Kelbrook Heads QLD 4590

Colors
6B429C
8869AF
B7A5CE
E3DAEB
F3F0F8

Requirements
Must have
• Logo & details listed above
Should not have
• No red or orange

```html
<!DOCTYPE html>
<html lang="en">
<head>
<meta charset="utf-8">
<title>Walk Beside The River – Business Card</title>
<link rel="stylesheet" href="https://fonts.googleapis.com/css2?family=Open+Sans:wght@400;600;700&display=swap">
<style>
  :root {
    --purple: #6B429C;
    --purple-mid: #8869AF;
    --lavender: #E3DAEB;
    --sun: #F0E52C;
    --sun-deep: #F2D21E;
    --sun-soft: #F7EE6A;
    --white: #FFFFFF;
    --ink: #1E1E1E;
    --backdrop: #DCDCDE;
  }
  * { box-sizing: border-box; margin: 0; padding: 0; }
  html, body {
    width: 1200px; height: 780px; overflow: hidden;
    background: var(--backdrop);
    font-family: "Open Sans", Arial, sans-serif;
  }
  .canvas { position: relative; width: 1200px; height: 780px; }

  .card {
    position: absolute; top: 230px;
    width: 520px; height: 320px;
    border-radius: 22px; overflow: hidden;
    box-shadow: 0 10px 28px rgba(0,0,0,0.22);
  }
  .card-front { left: 50px; background: var(--white); }
  .card-back  { left: 630px; }

  .front-shapes { position: absolute; inset: 0; }

  .brand {
    position: absolute; left: 40px; top: 38px;
    display: flex; align-items: center; gap: 10px;
  }
  .brand-dot { width: 16px; height: 16px; border-radius: 50%; background: var(--purple); }
  .brand-name { font-weight: 700; font-size: 20px; color: var(--purple); letter-spacing: 0.2px; }

  .name-tab {
    position: absolute; left: 0; top: 118px;
    width: 14px; height: 34px; background: var(--purple);
  }
  .person-name {
    position: absolute; left: 28px; top: 114px;
    font-weight: 700; font-size: 30px; color: var(--purple); line-height: 1.2;
  }
  .person-title {
    position: absolute; left: 28px; top: 156px;
    font-size: 15px; color: var(--ink);
  }

  .contact-list {
    position: absolute; left: 22px; top: 188px;
    list-style: none;
  }
  .contact-item {
    display: flex; align-items: center; gap: 8px;
    font-size: 13.5px; color: var(--ink); line-height: 22px;
    white-space: nowrap;
  }
  .contact-icon { width: 13px; height: 13px; flex: none; }

  .service {
    position: absolute; left: 300px; top: 254px;
    font-size: 14px; color: var(--ink); line-height: 19px;
    white-space: nowrap;
  }

  .back-fill { position: absolute; inset: 0; }
</style>
</head>
<body>
<main class="canvas">

  <section class="card card-front" aria-label="Business card front">
    <svg class="front-shapes" viewBox="0 0 520 320" width="520" height="320" aria-hidden="true">
      <path d="M0 282 L0 320 L520 320 L520 250 C480 288 420 304 360 306 L200 306 Z" fill="var(--sun)"/>
      <path d="M0 276 L186 276 L200 306 L0 306 Z" fill="var(--purple)"/>
      <path d="M0 270 L188 270 L190 273 L0 273 Z" fill="var(--sun)"/>
    </svg>

    <div class="brand">
      <span class="brand-dot"></span>
      <span class="brand-name">Walk Beside The River</span>
    </div>

    <span class="name-tab"></span>
    <h1 class="person-name">Danica Holloway</h1>
    <p class="person-title">CEO/Director</p>

    <ul class="contact-list">
      <li class="contact-item">
        <svg class="contact-icon" viewBox="0 0 16 16" aria-hidden="true"><path d="M4 1.5l2.2 3-1.3 1.6c.8 1.8 2.2 3.2 4 4l1.6-1.3 3 2.2-1.2 2.6C7 13.5 2.5 9 1.4 2.7z" fill="var(--purple)"/></svg>
        <span>0481 637 092</span>
      </li>
      <li class="contact-item">
        <svg class="contact-icon" viewBox="0 0 16 16" aria-hidden="true"><rect x="1" y="3" width="14" height="10" rx="1.5" fill="var(--purple)"/><path d="M1.5 4l6.5 5 6.5-5" stroke="var(--white)" stroke-width="1.4" fill="none"/></svg>
        <span>walkbesidetheriver@mailcove.com.au</span>
      </li>
      <li class="contact-item">
        <svg class="contact-icon" viewBox="0 0 16 16" aria-hidden="true"><path d="M8 1a5 5 0 0 0-5 5c0 3.8 5 9 5 9s5-5.2 5-9a5 5 0 0 0-5-5z" fill="var(--purple)"/><circle cx="8" cy="6" r="1.8" fill="var(--white)"/></svg>
        <span>PO Box 926 Kelbrook Heads QLD 4590</span>
      </li>
    </ul>

    <p class="service">Mental Health Support<br>Rosalind Tavener</p>
  </section>

  <section class="card card-back" aria-label="Business card back">
    <svg class="back-fill" viewBox="0 0 520 320" width="520" height="320" role="img" aria-label="Yellow star pattern background fading to light gold">
      <defs>
        <linearGradient id="backGlow" x1="0" y1="1" x2="1" y2="0">
          <stop offset="0" stop-color="var(--sun-deep)"/>
          <stop offset="0.55" stop-color="var(--sun)"/>
          <stop offset="1" stop-color="var(--sun-soft)"/>
        </linearGradient>
      </defs>
      <rect width="520" height="320" fill="url(#backGlow)"/>
    </svg>
  </section>

</main>
</body>
</html>
```